Computer Training in the Education sector - Letterhead

We need a new letter head to be designed for the company. We provide computer training fro the Education Sector, both primary and private tertiary providers. The colours will need to tie in with the website www.crossingthestream.co.nz.
The company name is Crossing the Stream with the tag line of Computer Training for Educators.
The footer will need to have the following detail...
0508 PCS MENTOR
021 839 415
www.crossingthestream.co.nz / training@crossingthestream.co.nz
Updates

Thanks for the designs so far.

Some have watermarks in the background. Please don't worry about using watermarks as I will not be using a watermark in in a final design.
Regards,
Roger

Thank you for all the designs and the effort. There was some great concepts that came through.

Cheers
Roger

Industry/Entity Type

Computer

```html
<!DOCTYPE html>
<html lang="en">
<head>
<meta charset="utf-8">
<title>Crossing the Stream – Letterhead</title>
<link rel="stylesheet" href="https://fonts.googleapis.com/css2?family=Arimo:wght@400;700&display=swap">
<style>
  :root {
    --paper: #ffffff;
    --ink: #2b2b2b;
    --ink-soft: #3a3a3a;
    --brand-blue: #2f78be;
    --rule: #6b6b6b;
    --faint-mark: #e9eef2;
  }
  * { margin: 0; padding: 0; box-sizing: border-box; }
  html, body {
    width: 1034px;
    height: 1200px;
    overflow: hidden;
    background: var(--paper);
  }
  .letterhead {
    position: relative;
    width: 1034px;
    height: 1200px;
    background: var(--paper);
    font-family: "Arimo", Arial, sans-serif;
    color: var(--ink);
  }
  .brand {
    position: absolute;
    left: 54px;
    top: 48px;
    display: flex;
    align-items: center;
    gap: 14px;
  }
  .brand-dot {
    width: 22px;
    height: 22px;
    border-radius: 50%;
    background: var(--brand-blue);
  }
  .brand-name {
    font-size: 30px;
    font-weight: 400;
    line-height: 1.1;
    color: var(--brand-blue);
  }
  .contact {
    position: absolute;
    left: 650px;
    top: 52px;
    padding-left: 20px;
    border-left: 1px solid var(--rule);
    list-style: none;
    font-size: 17px;
    letter-spacing: 0.5px;
    color: var(--ink-soft);
  }
  .contact-item {
    display: flex;
    align-items: center;
    gap: 6px;
    height: 25px;
  }
  .contact-icon {
    width: 14px;
    height: 14px;
    flex: none;
  }
  .footer-mark {
    position: absolute;
    left: 64px;
    top: 1036px;
    width: 146px;
    height: 146px;
    border-radius: 50%;
    border: 14px solid var(--faint-mark);
  }
  .tagline {
    position: absolute;
    left: 122px;
    top: 1105px;
    font-size: 18px;
    font-weight: 700;
    letter-spacing: 2px;
    color: var(--ink);
  }
</style>
</head>
<body>
<main class="letterhead">
  <header class="brand">
    <span class="brand-dot" aria-hidden="true"></span>
    <span class="brand-name">Crossing<br>the Stream</span>
  </header>

  <ul class="contact">
    <li class="contact-item">
      <svg class="contact-icon" viewBox="0 0 14 14" aria-hidden="true"><circle cx="7" cy="7" r="6" fill="none" stroke="#3a3a3a" stroke-width="1"/><path d="M5 3.5 L6.3 5.2 L5.6 6.2 Q6.4 7.8 7.8 8.4 L8.8 7.7 L10.5 9 L9.6 10.4 Q6 10 3.6 5.2 Z" fill="#3a3a3a"/></svg>
      <span>0508 PCS MENTOR</span>
    </li>
    <li class="contact-item">
      <svg class="contact-icon" viewBox="0 0 14 14" aria-hidden="true"><circle cx="7" cy="7" r="6" fill="none" stroke="#3a3a3a" stroke-width="1"/><path d="M5 3.5 L6.3 5.2 L5.6 6.2 Q6.4 7.8 7.8 8.4 L8.8 7.7 L10.5 9 L9.6 10.4 Q6 10 3.6 5.2 Z" fill="#3a3a3a"/></svg>
      <span>021 839 415</span>
    </li>
    <li class="contact-item">
      <svg class="contact-icon" viewBox="0 0 14 14" aria-hidden="true"><path d="M1 6 L7 2 L13 6 V12 H1 Z" fill="#3a3a3a"/><path d="M1.5 6.3 L7 9.5 L12.5 6.3" fill="none" stroke="#fff" stroke-width="1"/></svg>
      <span>training@crossingthestream.co.nz</span>
    </li>
    <li class="contact-item">
      <svg class="contact-icon" viewBox="0 0 14 14" aria-hidden="true" fill="none" stroke="#3a3a3a" stroke-width="1"><circle cx="7" cy="7" r="6"/><ellipse cx="7" cy="7" rx="2.6" ry="6"/><path d="M1 7 H13 M2 4 H12 M2 10 H12"/></svg>
      <span>www.crossingthestream.co.nz</span>
    </li>
  </ul>

  <footer>
    <div class="footer-mark" aria-hidden="true"></div>
    <p class="tagline">Computer Training for Educators</p>
  </footer>
</main>
</body>
</html>
```